Residential Remodeling Contractor needs updated business card

I need a new design for my business card.
Name of the company is Ridgefell Construction. I need a card that commands presence, strength, integrity. I have been in business for 28 years. I am a Residential Remodeling Contractor that covers all aspects of a residential remodel and build.

```html
<!DOCTYPE html>
<html lang="en">
<head>
<meta charset="utf-8">
<title>Ridgefell Construction – Business Card</title>
<link href="https://fonts.googleapis.com/css2?family=Arimo:wght@400;700&display=swap" rel="stylesheet">
<style>
  :root {
    --stage: #2a2a2c;
    --card-blue: #1b3f85;
    --card-blue-light: #24509e;
    --ink: #ffffff;
    --ink-soft: rgba(255, 255, 255, 0.85);
    --rule: rgba(255, 255, 255, 0.7);
  }
  * { margin: 0; padding: 0; box-sizing: border-box; }
  html, body {
    width: 1200px;
    height: 801px;
    overflow: hidden;
    background: var(--stage);
    font-family: "Arimo", Arial, sans-serif;
    color: var(--ink);
  }
  .sheet {
    width: 1200px;
    height: 801px;
    display: flex;
    align-items: center;
    justify-content: center;
    gap: 40px;
  }
  .card {
    width: 540px;
    height: 309px;
    border-radius: 22px;
    background: linear-gradient(135deg, var(--card-blue-light) 0%, var(--card-blue) 60%);
    position: relative;
    overflow: hidden;
  }

  /* Wordmark */
  .wordmark {
    display: flex;
    align-items: center;
    gap: 12px;
  }
  .wordmark-dot {
    width: 14px;
    height: 14px;
    background: var(--ink);
    flex: none;
  }
  .wordmark-name {
    font-weight: 700;
    text-transform: uppercase;
    letter-spacing: 0.06em;
    line-height: 1.05;
    color: var(--ink);
  }

  /* Contact face */
  .card-front .wordmark {
    position: absolute;
    top: 50px;
    left: 120px;
  }
  .card-front .wordmark-name { font-size: 26px; }

  .front-details {
    position: absolute;
    top: 152px;
    left: 36px;
    right: 24px;
    display: flex;
    align-items: center;
  }
  .holder {
    text-align: right;
    padding-right: 16px;
    white-space: nowrap;
  }
  .holder-name {
    font-size: 19px;
    font-weight: 700;
    text-transform: uppercase;
    letter-spacing: 0.02em;
  }
  .holder-role {
    font-size: 13px;
    color: var(--ink-soft);
    margin-top: 4px;
  }
  .divider {
    width: 1px;
    height: 64px;
    background: var(--rule);
    flex: none;
  }
  .contacts {
    list-style: none;
    padding-left: 16px;
    font-size: 13px;
    line-height: 1.65;
    white-space: nowrap;
  }
  .contacts li {
    display: flex;
    align-items: center;
    gap: 8px;
  }
  .contacts svg { width: 11px; height: 11px; fill: var(--ink); flex: none; }

  .address {
    position: absolute;
    bottom: 42px;
    left: 0;
    right: 0;
    text-align: center;
    font-size: 13px;
    color: var(--ink-soft);
    letter-spacing: 0.02em;
  }

  /* Logo face */
  .card-back {
    display: flex;
    align-items: center;
    justify-content: center;
  }
  .card-back .wordmark { gap: 18px; }
  .card-back .wordmark-dot { width: 22px; height: 22px; }
  .card-back .wordmark-name { font-size: 38px; }
</style>
</head>
<body>
<main class="sheet">
  <section class="card card-front" aria-label="Business card, contact side">
    <div class="wordmark">
      <span class="wordmark-dot"></span>
      <span class="wordmark-name">Ridgefell<br>Construction</span>
    </div>

    <div class="front-details">
      <div class="holder">
        <p class="holder-name">Marco Delvane</p>
        <p class="holder-role">Owner &amp; Manager</p>
      </div>
      <span class="divider"></span>
      <ul class="contacts">
        <li>
          <svg viewBox="0 0 24 24" aria-hidden="true"><path d="M6.6 10.8a15.1 15.1 0 0 0 6.6 6.6l2.2-2.2a1 1 0 0 1 1-.25 11.4 11.4 0 0 0 3.6.57 1 1 0 0 1 1 1V20a1 1 0 0 1-1 1A17 17 0 0 1 3 4a1 1 0 0 1 1-1h3.5a1 1 0 0 1 1 1c0 1.25.2 2.45.57 3.6a1 1 0 0 1-.25 1z"/></svg>
          555 014 2287
        </li>
        <li>
          <svg viewBox="0 0 24 24" aria-hidden="true"><path d="M2 5h20v14H2z"/><path d="M2 5l10 8 10-8" fill="none" stroke="#1b3f85" stroke-width="2"/></svg>
          info@ridgefellconstruction.com
        </li>
        <li>
          <svg viewBox="0 0 24 24" aria-hidden="true"><circle cx="12" cy="12" r="10"/></svg>
          www.ridgefellconstruction.com
        </li>
      </ul>
    </div>

    <p class="address">P.O. Box 418&nbsp; Harlow Lane Brookfield AB, T4R 2K9</p>
  </section>

  <section class="card card-back" aria-label="Business card, logo side">
    <div class="wordmark">
      <span class="wordmark-dot"></span>
      <span class="wordmark-name">Ridgefell<br>Construction</span>
    </div>
  </section>
</main>
</body>
</html>
```